RWT Fittings Ltd Business Cards

We need a business card with our business logo. We provide window and door installations on high-rises in west coast British Colombia, Canada.

I would like my business information and details on one side of the card, and the other side the company name with logo

Target Market(s)

General Contractors

Industry/Entity Type

Construction

Contact Information for Business Card

one side i want my company name and logo in the dark theme logo that i provided

Requirements
Must have
• Marco Peltieri, 16045518293, RWTFittings@mailbox-demo.com, 1407-5194 Linden Row Burnaby BC, V5H 2K9, Owner & Manager

```html
<!DOCTYPE html>
<html lang="en">
<head>
<meta charset="utf-8">
<title>RWT Fittings Ltd – Business Cards</title>
<link href="https://fonts.googleapis.com/css2?family=Roboto:wght@400;700&display=swap" rel="stylesheet">
<style>
  :root {
    --stage: #232323;
    --card: #1f2024;
    --card-edge: #141518;
    --grey-band: #9c9c9c;
    --blue-band: #29a9e1;
    --brand-blue: #29a9e1;
    --emboss: #2e3035;
    --text-light: #ffffff;
  }
  * { margin: 0; padding: 0; box-sizing: border-box; }
  html, body {
    width: 1200px; height: 780px; overflow: hidden;
    background: var(--stage);
    font-family: "Roboto", Arial, sans-serif;
  }
  .canvas {
    position: relative; width: 1200px; height: 780px;
  }
  .card {
    position: absolute;
    width: 525px; height: 300px;
    background: var(--card);
    border-radius: 3px;
    box-shadow: 0 4px 0 var(--card-edge), 0 18px 40px rgba(0,0,0,.55);
    overflow: hidden;
  }
  .card--front { left: 45px; top: 240px; }
  .card--back  { left: 630px; top: 240px; }

  .brand {
    position: absolute;
    display: flex; align-items: center; gap: 10px;
    font-weight: 700; white-space: nowrap;
  }
  .brand__mark { display: block; }
  .card--front .brand { left: 235px; top: 58px; font-size: 27px; color: var(--brand-blue); }
  .card--front .brand__mark { width: 22px; height: 22px; background: var(--brand-blue); }

  .card--back .brand {
    left: 50%; top: 50%; transform: translate(-50%, -50%);
    font-size: 38px; color: var(--emboss);
  }
  .card--back .brand__mark { width: 30px; height: 30px; background: var(--emboss); }

  .name-band {
    position: absolute; left: 0; top: 118px;
    width: 235px; height: 72px;
    background: var(--grey-band);
    color: var(--text-light);
    padding: 12px 0 0 34px;
  }
  .name-band__name { font-size: 24px; font-weight: 700; line-height: 1.1; }
  .name-band__role { font-size: 13px; font-weight: 400; margin-top: 4px; }

  .contact-band {
    position: absolute; left: 248px; top: 190px;
    width: 277px; height: 64px;
    background: var(--blue-band);
    color: var(--text-light);
    padding: 10px 0 0 18px;
    font-size: 14px;
  }
  .contact-band__row { display: flex; align-items: center; gap: 8px; line-height: 22px; }
  .contact-band__row svg { width: 13px; height: 13px; flex: none; }

  .address {
    position: absolute; left: 34px; top: 262px;
    color: var(--text-light); font-size: 13.5px;
  }
</style>
</head>
<body>
<main class="canvas">

  <section class="card card--front" aria-label="Business card, contact side">
    <div class="brand"><span class="brand__mark"></span><span>RWT Fittings Ltd</span></div>

    <div class="name-band">
      <div class="name-band__name">Marco Peltieri</div>
      <div class="name-band__role">Owner &amp; Manager</div>
    </div>

    <div class="contact-band">
      <div class="contact-band__row">
        <svg viewBox="0 0 24 24" aria-hidden="true"><path fill="#fff" d="M6.6 10.8a15.1 15.1 0 0 0 6.6 6.6l2.2-2.2a1 1 0 0 1 1-.25 11.4 11.4 0 0 0 3.6.57 1 1 0 0 1 1 1V20a1 1 0 0 1-1 1A17 17 0 0 1 3 4a1 1 0 0 1 1-1h3.5a1 1 0 0 1 1 1c0 1.25.2 2.45.57 3.57a1 1 0 0 1-.25 1z"/></svg>
        <span>16045518293</span>
      </div>
      <div class="contact-band__row">
        <svg viewBox="0 0 24 24" aria-hidden="true"><path fill="#fff" d="M3 5h18a1 1 0 0 1 1 1v12a1 1 0 0 1-1 1H3a1 1 0 0 1-1-1V6a1 1 0 0 1 1-1zm9 7.5L4 7.2V17h16V7.2z"/></svg>
        <span>RWTFittings@mailbox-demo.com</span>
      </div>
    </div>

    <div class="address">1407-5194 Linden Row Burnaby BC, V5H 2K9</div>
  </section>

  <section class="card card--back" aria-label="Business card, brand side">
    <div class="brand"><span class="brand__mark"></span><span>RWT Fittings Ltd</span></div>
  </section>

</main>
</body>
</html>
```